KRV Business Card

Looking for a business card for my restaurant group I own. Four different concepts:

Copperfield Alehouse
Bristow Alehouse
Tanager's Stone Hearth Kitchen
Pellston Patty Company

Card doesn't need to include all the logos.

```html
<!DOCTYPE html>
<html lang="en">
<head>
<meta charset="utf-8">
<title>KRV Business Card</title>
<link href="https://fonts.googleapis.com/css2?family=Lato:wght@400;700&display=swap" rel="stylesheet">
<style>
  :root {
    --backdrop: #2b2b2d;
    --card-top: #1c1c1d;
    --card-bottom: #0b0b0c;
    --gold: #d9b263;
    --silver: #c9c9c9;
    --white: #f1f1f1;
    --rule: #6d6d6d;
  }
  * { margin: 0; padding: 0; box-sizing: border-box; }
  html, body {
    width: 1200px; height: 900px; overflow: hidden;
    background: var(--backdrop);
    font-family: "Lato", sans-serif;
  }
  .cards {
    position: absolute; inset: 0;
    display: flex; align-items: center; justify-content: center; gap: 40px;
  }
  .card {
    position: relative;
    width: 540px; height: 308px;
    background: linear-gradient(160deg, var(--card-top), var(--card-bottom));
    overflow: hidden;
  }
  .card__band {
    position: absolute; left: 0; right: 0; bottom: 0; height: 9px;
    background: var(--gold);
  }

  /* Front */
  .card--front { display: flex; flex-direction: column; align-items: center; padding-top: 52px; }
  .brand { text-align: center; color: var(--gold); font-weight: 700; }
  .brand__initials { display: block; font-size: 46px; letter-spacing: 4px; line-height: 1; }
  .brand__name { display: block; margin-top: 14px; font-size: 19px; letter-spacing: 3px; text-transform: uppercase; line-height: 1.3; }
  .front__rule { width: 290px; height: 1px; background: var(--rule); margin: 18px 0 12px; }
  .concepts {
    list-style: none; text-align: center; color: var(--silver);
    font-size: 11.5px; font-weight: 700; letter-spacing: 0.6px; text-transform: uppercase; line-height: 1.7;
  }
  .concepts span { margin: 0 6px; font-weight: 400; }

  /* Back */
  .card--back { padding: 110px 0 0 0; }
  .back__main { display: flex; align-items: center; }
  .person { width: 250px; text-align: right; padding-right: 22px; }
  .person__name { color: var(--gold); font-size: 19px; font-weight: 400; letter-spacing: 0.5px; text-transform: uppercase; }
  .person__title { color: var(--white); font-size: 14px; margin-top: 2px; }
  .back__divider { width: 1px; height: 56px; background: var(--rule); }
  .contact { list-style: none; padding-left: 22px; color: var(--white); font-size: 14px; line-height: 1.5; }
  .contact li { display: flex; align-items: center; gap: 8px; }
  .contact svg { width: 11px; height: 11px; fill: var(--gold); flex: none; }
  .address { color: var(--white); font-size: 14px; text-align: center; margin-top: 52px; }
</style>
</head>
<body>
  <main class="cards">
    <section class="card card--front" aria-label="Card front">
      <div class="brand">
        <span class="brand__initials">KRV</span>
        <span class="brand__name">Kerrville Hospitality Group</span>
      </div>
      <div class="front__rule"></div>
      <ul class="concepts">
        <li>Copperfield Alehouse<span>|</span>Bristow Alehouse</li>
        <li>Tanager's Stone Hearth Kitchen<span>|</span>Pellston Patty Company</li>
      </ul>
      <div class="card__band"></div>
    </section>

    <section class="card card--back" aria-label="Card back">
      <div class="back__main">
        <div class="person">
          <h1 class="person__name">Daniel Reyes</h1>
          <p class="person__title">Managing Director</p>
        </div>
        <div class="back__divider"></div>
        <ul class="contact">
          <li>
            <svg viewBox="0 0 16 16" aria-hidden="true"><path d="M3 1h3l1.5 4-2 1.3a9 9 0 0 0 4.2 4.2L11 8.5l4 1.5v3a2 2 0 0 1-2 2C6.4 15 1 9.6 1 3a2 2 0 0 1 2-2z"/></svg>
            044-555 218 630
          </li>
          <li>
            <svg viewBox="0 0 16 16" aria-hidden="true"><path d="M1 3h14v1.2L8 9 1 4.2z"/><path d="M1 5.8 8 10.6l7-4.8V13H1z"/></svg>
            info@kerrvillehg.com
          </li>
          <li>
            <svg viewBox="0 0 16 16" aria-hidden="true"><circle cx="8" cy="8" r="7"/><path d="M1 8h14M8 1c3 3 3 11 0 14M8 1c-3 3-3 11 0 14" stroke="#111" stroke-width="1.1" fill="none"/></svg>
            www.kerrvillehg.com
          </li>
        </ul>
      </div>
      <p class="address">118 Harbor Lane, 78028, Midland</p>
      <div class="card__band"></div>
    </section>
  </main>
</body>
</html>
```